International oil and gas consultancy needs a business card design

We need a business card design for a new oil and gas consultancy business based in Perth Australia. This is a professional services business and needs a moderately conservative type of business card. The business card also needs to be simple and uncluttered. The colour of the business logo is dark red (see attached file).
The front of the card should have a white background and mainly black lettering and perhaps some use of dark red and/or grey (your choice).
The back of the card should have a light grey background with dark red, black and or both dark red & black lettering (your choice).
Please find attached a clear brief of how I would like the business card designed.
Updates

Hello Everyone, I have slightly modified the brief. The main change is to incorporate some dark red and grey colours into the card, while still keeping the black lettering dominant. I have made the changes in the attached detailed brief document. Regards

Please note, the front of the card must say Harbour Ledger Services (in addition to the logo).

Industry/Entity Type

Conservative

Requirements
Must have
• brief has been updated. please refer to attachment for details.

Front of the card MUST say Harbour Ledger Services (in addition to the logo)

```html
<!DOCTYPE html>
<html lang="en">
<head>
<meta charset="utf-8">
<title>Harbour Ledger Services – Business Card</title>
<link href="https://fonts.googleapis.com/css2?family=Michroma&display=swap" rel="stylesheet">
<style>
  :root {
    --backdrop: #c3c8cf;
    --card-white: #ffffff;
    --card-grey: #e4e4e4;
    --brand-red: #931b1e;
    --ink: #2f2f2f;
    --swoosh: #333333;
    --on-red: #ffffff;
  }
  * { margin: 0; padding: 0; box-sizing: border-box; }
  html, body {
    width: 1200px;
    height: 887px;
    overflow: hidden;
    background: var(--backdrop);
    font-family: "Michroma", sans-serif;
  }
  .card {
    position: absolute;
    left: 80px;
    top: 146px;
    width: 1040px;
    height: 594px;
    background: radial-gradient(ellipse at 50% 60%, var(--card-white) 0%, var(--card-grey) 100%);
    overflow: hidden;
    box-shadow: 0 6px 18px rgba(0,0,0,0.18);
  }
  .card-band {
    position: absolute;
    inset: 0;
    width: 100%;
    height: 100%;
  }
  .brand {
    position: absolute;
    left: 76px;
    top: 92px;
    display: flex;
    align-items: center;
    gap: 14px;
    color: var(--brand-red);
    font-size: 27px;
    letter-spacing: 1px;
  }
  .brand-mark {
    width: 22px;
    height: 22px;
    background: var(--brand-red);
  }
  .person {
    position: absolute;
    right: 40px;
    top: 296px;
    text-align: right;
    color: var(--ink);
  }
  .person-name {
    font-size: 21px;
    letter-spacing: 3px;
    text-transform: uppercase;
  }
  .person-title {
    margin-top: 8px;
    font-size: 15px;
    letter-spacing: 2.5px;
    font-variant: small-caps;
  }
  .contact {
    position: absolute;
    color: var(--on-red);
    font-size: 14px;
    letter-spacing: 1.2px;
    font-variant: small-caps;
    display: flex;
    gap: 16px;
    white-space: nowrap;
  }
  .contact-line-1 { left: 170px; top: 450px; }
  .contact-line-2 { left: 50px; top: 484px; }
  .contact-item {
    display: inline-flex;
    align-items: center;
    gap: 6px;
  }
  .contact-icon { width: 15px; height: 15px; flex: none; }
</style>
</head>
<body>
  <main class="card">
    <svg class="card-band" viewBox="0 0 1040 594" preserveAspectRatio="none" aria-hidden="true">
      <path d="M0,292 C250,372 520,392 720,382 C860,376 960,398 1040,428 L1040,594 L0,594 Z" fill="var(--brand-red)"/>
      <path d="M0,274 C250,350 520,370 720,360 C860,354 960,380 1030,420" fill="none" stroke="var(--swoosh)" stroke-width="6" stroke-linecap="round"/>
    </svg>

    <div class="brand">
      <span class="brand-mark"></span>
      <span class="brand-name">Harbour Ledger Services</span>
    </div>

    <div class="person">
      <div class="person-name">Martin Hale</div>
      <div class="person-title">Managing Director</div>
    </div>

    <div class="contact contact-line-1">
      <span class="contact-item">
        <svg class="contact-icon" viewBox="0 0 16 16"><circle cx="8" cy="8" r="8" fill="var(--on-red)"/><path d="M4 8.5 L8 4.5 L12 8.5 V12 H4 Z" fill="var(--brand-red)"/></svg>
        Level 4, 210 Quay Street, Perth WA 6000
      </span>
      <span class="contact-item">
        <svg class="contact-icon" viewBox="0 0 16 16"><circle cx="8" cy="8" r="8" fill="var(--on-red)"/><circle cx="8" cy="8" r="5" fill="none" stroke="var(--brand-red)" stroke-width="1.2"/><path d="M3 8 H13 M8 3 V13" stroke="var(--brand-red)" stroke-width="1.2"/></svg>
        www.harbourledger.com
      </span>
    </div>

    <div class="contact contact-line-2">
      <span class="contact-item">
        <svg class="contact-icon" viewBox="0 0 16 16"><circle cx="8" cy="8" r="8" fill="var(--on-red)"/><path d="M5 4 L7 6 L6 7.5 Q7.5 9.5 8.5 10 L10 9 L12 11 L10.5 12.5 Q6 11.5 3.5 5.5 Z" fill="var(--brand-red)"/></svg>
        08-6120-4410
      </span>
      <span class="contact-item">
        <svg class="contact-icon" viewBox="0 0 16 16"><circle cx="8" cy="8" r="8" fill="var(--on-red)"/><rect x="5.5" y="3.5" width="5" height="9" rx="1" fill="var(--brand-red)"/></svg>
        0412-558-903
      </span>
      <span class="contact-item">
        <svg class="contact-icon" viewBox="0 0 16 16"><circle cx="8" cy="8" r="8" fill="var(--on-red)"/><rect x="4" y="6" width="8" height="6" fill="var(--brand-red)"/><rect x="5.5" y="3.5" width="5" height="3" fill="var(--brand-red)"/></svg>
        08-6120-4411
      </span>
      <span class="contact-item">
        <svg class="contact-icon" viewBox="0 0 16 16"><circle cx="8" cy="8" r="8" fill="var(--on-red)"/><rect x="3.5" y="5" width="9" height="6" fill="var(--brand-red)"/><path d="M3.5 5 L8 8.5 L12.5 5" fill="none" stroke="var(--on-red)" stroke-width="0.9"/></svg>
        martin@harbourledger.com
      </span>
    </div>
  </main>
</body>
</html>
```